Need help in designing new business card utilizing our new logo.

BuildMark Solutions works with Construction Business Owners, Managers & IT Professionals to strengthen software usage and increase user productivity.

Our Construction Accounting and Mobile Field Management Software Clients engage with us in the following areas:

New Software Implementations
Software Re-Implementations
Redesigning Software Usage at the User Level
Project Coordination & Management
Continued Software Support

Old tag line:
Weighing Options - Implementing Solutions

www.buildmark-solutions.example

Ridge 4 is a product, but not needed for a new business card.

```html
<!DOCTYPE html>
<html lang="en">
<head>
<meta charset="utf-8">
<title>BuildMark Solutions – Business Card</title>
<link rel="stylesheet" href="https://fonts.googleapis.com/css2?family=Montserrat:wght@400;500;600&display=swap">
<style>
  :root {
    --backdrop: #161616;
    --card: #232323;
    --card-edge: #2a2a2a;
    --brand-blue: #2f3db0;
    --text-light: #f2f2f2;
    --front-mark: #8a8a8a;
  }
  * { box-sizing: border-box; margin: 0; padding: 0; }
  html, body { width: 1200px; height: 900px; overflow: hidden; }
  body {
    background: var(--backdrop);
    font-family: "Montserrat", sans-serif;
    color: var(--text-light);
    position: relative;
  }
  .card {
    position: absolute;
    left: 250px;
    width: 700px;
    height: 400px;
    background: linear-gradient(160deg, var(--card-edge), var(--card));
    border-bottom: 8px solid var(--brand-blue);
  }
  .card--front { top: 40px; }
  .card--back { top: 470px; }

  .brand-square {
    width: 46px;
    height: 46px;
    background: currentColor;
    border-radius: 4px;
    flex: none;
  }
  .brand-name {
    font-weight: 600;
    font-size: 34px;
    letter-spacing: 0.5px;
    white-space: nowrap;
  }

  .front-brand {
    position: absolute;
    inset: 0;
    display: flex;
    align-items: center;
    justify-content: center;
    gap: 18px;
    color: var(--front-mark);
  }

  .back-brand {
    position: absolute;
    left: 40px;
    top: 150px;
    display: flex;
    align-items: center;
    gap: 12px;
    color: var(--brand-blue);
  }
  .back-brand .brand-square { width: 32px; height: 32px; }
  .back-brand .brand-name { font-size: 21px; }

  .divider {
    position: absolute;
    left: 360px;
    top: 90px;
    width: 2px;
    height: 200px;
    background: var(--brand-blue);
  }

  .contact {
    position: absolute;
    left: 382px;
    top: 82px;
    right: 16px;
  }
  .contact__name {
    color: var(--brand-blue);
    font-weight: 600;
    font-size: 22px;
    letter-spacing: 1px;
    white-space: nowrap;
  }
  .contact__role {
    font-size: 15px;
    margin-bottom: 16px;
  }
  .contact__list { list-style: none; }
  .contact__item {
    display: flex;
    align-items: center;
    gap: 9px;
    font-size: 13px;
    line-height: 22px;
    white-space: nowrap;
  }
  .contact__item svg { width: 12px; height: 12px; flex: none; }
  .contact__address {
    margin-top: 16px;
    font-size: 15px;
    line-height: 22px;
    font-style: normal;
    white-space: nowrap;
  }
</style>
</head>
<body>
  <section class="card card--front" aria-label="Card front">
    <div class="front-brand">
      <span class="brand-square" aria-hidden="true"></span>
      <span class="brand-name">BuildMark Solutions</span>
    </div>
  </section>

  <section class="card card--back" aria-label="Card back">
    <div class="back-brand">
      <span class="brand-square" aria-hidden="true"></span>
      <span class="brand-name">BuildMark Solutions</span>
    </div>
    <div class="divider" aria-hidden="true"></div>
    <div class="contact">
      <p class="contact__name">Dana R. Whitfield</p>
      <p class="contact__role">Owner</p>
      <ul class="contact__list">
        <li class="contact__item">
          <svg viewBox="0 0 12 12" aria-hidden="true"><path d="M2 1h2.5l1 3-1.5 1a6 6 0 0 0 3 3l1-1.5 3 1V10a1 1 0 0 1-1 1A10 10 0 0 1 1 2a1 1 0 0 1 1-1z" fill="var(--brand-blue)"/></svg>
          800-555-0142 ext.100
        </li>
        <li class="contact__item">
          <svg viewBox="0 0 12 12" aria-hidden="true"><rect x="3" y="0.5" width="6" height="11" rx="1" fill="none" stroke="var(--brand-blue)"/><circle cx="6" cy="9.5" r="0.7" fill="var(--brand-blue)"/></svg>
          518-555-0193
        </li>
        <li class="contact__item">
          <svg viewBox="0 0 12 12" aria-hidden="true"><rect x="0.5" y="2.5" width="11" height="7" fill="none" stroke="var(--brand-blue)"/><path d="M0.5 2.5 6 6.5l5.5-4" fill="none" stroke="var(--brand-blue)"/></svg>
          dana@buildmark-solutions.example
        </li>
        <li class="contact__item">
          <svg viewBox="0 0 12 12" aria-hidden="true"><circle cx="6" cy="6" r="5.3" fill="none" stroke="var(--brand-blue)"/><ellipse cx="6" cy="6" rx="2.3" ry="5.3" fill="none" stroke="var(--brand-blue)"/><path d="M0.7 6h10.6" stroke="var(--brand-blue)"/></svg>
          www.buildmark-solutions.example
        </li>
      </ul>
      <address class="contact__address">
        14B Harbor Lane - PMB 118<br>
        Brookfield NY 12000
      </address>
    </div>
  </section>
</body>
</html>
```